Corvane Freight Company Business Card Design

We are a company that delivers natural saltwater (from the ocean) to aquarium companies, restaurants and home marine tanks. I would like a new business card to suit.

Must include Name, company name, abn, contact number and website as well as logo (see attached).

Looking for a design that stands out, has a clean but unique appearance.

Double and single sided entries welcome

Business

• Logo

```html
<!DOCTYPE html>
<html lang="en">
<head>
<meta charset="utf-8">
<title>Corvane Freight Company – Business Card</title>
<link rel="stylesheet" href="https://fonts.googleapis.com/css2?family=Arimo:wght@400&family=Open+Sans:wght@400;600;700&display=swap">
<style>
  :root {
    --backdrop: #3a2e29;
    --card-white: #ffffff;
    --sky: #55c9f3;
    --sky-light: #5ccdf5;
    --brand-blue: #1a8fd6;
    --deep-blue: #0a5fb0;
    --ink: #555a5f;
    --ink-soft: #6a6f74;
    --divider: #b9bcbf;
  }
  * { box-sizing: border-box; margin: 0; padding: 0; }
  html, body {
    width: 1200px; height: 471px; overflow: hidden;
    background: var(--backdrop);
    font-family: "Open Sans", Arial, sans-serif;
  }
  .canvas { position: relative; width: 1200px; height: 471px; }

  .card {
    position: absolute;
    border-radius: 18px;
    overflow: hidden;
  }

  /* Front */
  .card-front {
    left: 45px; top: 77px; width: 520px; height: 296px;
    background: var(--card-white);
  }
  .front-brand {
    position: absolute; left: 20px; top: 118px; width: 240px;
    color: var(--brand-blue);
    font-weight: 600; font-size: 28px; line-height: 32px;
    text-align: center;
  }
  .front-divider {
    position: absolute; left: 316px; top: 50px; width: 2px; height: 174px;
    background: linear-gradient(to bottom, rgba(185,188,191,0), var(--divider) 20%, var(--divider) 80%, rgba(185,188,191,0));
  }
  .contact {
    position: absolute; left: 336px; top: 61px; right: 16px;
    color: var(--ink);
    font-family: "Arimo", Arial, sans-serif;
  }
  .contact-name { font-size: 20px; line-height: 24px; }
  .contact-title { font-size: 15px; line-height: 20px; color: var(--ink-soft); }
  .contact-lines { margin-top: 17px; }
  .contact-line {
    display: flex; align-items: center; gap: 6px;
    font-size: 14.5px; line-height: 21px; white-space: nowrap;
  }
  .contact-line svg { width: 11px; height: 11px; flex: none; }
  .contact-address { margin-top: 11px; font-size: 14.5px; line-height: 19px; }

  .strip-light {
    position: absolute; left: 0; bottom: 0; width: 260px; height: 17px;
    background: var(--sky-light);
  }
  .band-abn {
    position: absolute; right: 0; bottom: 0; width: 276px; height: 31px;
    background: var(--deep-blue);
    clip-path: polygon(31px 0, 100% 0, 100% 100%, 0 100%);
    color: #ffffff; font-family: "Arimo", Arial, sans-serif;
    font-size: 14px; line-height: 31px;
    padding-left: 92px;
  }

  /* Back */
  .card-back {
    left: 610px; top: 73px; width: 525px; height: 300px;
    background: var(--sky);
  }
  .back-brand {
    position: absolute; left: 0; right: 0; top: 112px;
    color: #ffffff; font-weight: 600;
    font-size: 52px; line-height: 58px; text-align: center;
  }
</style>
</head>
<body>
<div class="canvas">

  <section class="card card-front" aria-label="Card front">
    <div class="front-brand">Corvane Freight Company</div>
    <div class="front-divider"></div>

    <div class="contact">
      <div class="contact-name">Your Name</div>
      <div class="contact-title">Title</div>
      <div class="contact-lines">
        <div class="contact-line">
          <svg viewBox="0 0 12 12" aria-hidden="true">
            <path d="M3 1 L5 3.2 L4 4.6 C4.6 6 6 7.4 7.4 8 L8.8 7 L11 9 L9.8 10.6 C6 10.6 1.4 6 1.4 2.2 Z" fill="var(--brand-blue)"/>
          </svg>
          <span>123-456-7892</span>
        </div>
        <div class="contact-line">
          <svg viewBox="0 0 12 12" aria-hidden="true">
            <circle cx="6" cy="6" r="5" fill="none" stroke="var(--brand-blue)" stroke-width="1.2"/>
            <ellipse cx="6" cy="6" rx="2.2" ry="5" fill="none" stroke="var(--brand-blue)" stroke-width="1"/>
            <line x1="1" y1="6" x2="11" y2="6" stroke="var(--brand-blue)" stroke-width="1"/>
          </svg>
          <span>www.corvane.com</span>
        </div>
      </div>
      <div class="contact-address">Street Name, City Name<br>State, Zip Code</div>
    </div>

    <div class="strip-light"></div>
    <div class="band-abn">ABN: 123456789</div>
  </section>

  <section class="card card-back" aria-label="Card back">
    <div class="back-brand">Corvane Freight<br>Company</div>
  </section>

</div>
</body>
</html>
```